Looking for a modern, Professional business card design

We have a simple business card, but are looking for a more modern, professional look. A sample of the basic card is attached as well as the logo. We would also like to add that we offer:
Struggling with your finances?
- Learn to become debt free
- Discover the power of cash
- Control your money instead of it controlling you
Let us help you achieve a new level of financial freedom!
Also, we would like to have a "SPECIAL OFFER!: FREE 30 minute consultation"
Financial Planning

```html
<!DOCTYPE html>
<html lang="en">
<head>
<meta charset="utf-8">
<title>Clearpath Coaching – Business Card</title>
<link rel="stylesheet" href="https://fonts.googleapis.com/css2?family=Questrial&family=Russo+One&display=swap">
<style>
  :root {
    --page: #3a3a3c;
    --card-white: #ffffff;
    --card-black: #0b0b0b;
    --green: #7cc242;
    --green-deep: #4a9a2a;
    --ink: #1a1a1a;
    --muted: #9a9a9a;
    --body-font: "Questrial", sans-serif;
    --display-font: "Russo One", sans-serif;
  }
  * { box-sizing: border-box; margin: 0; padding: 0; }
  html, body { width: 1200px; height: 900px; overflow: hidden; }
  body {
    background: var(--page);
    font-family: var(--body-font);
    color: var(--ink);
    position: relative;
  }
  .card {
    position: absolute;
    left: 260px;
    width: 680px;
    height: 388px;
    border-radius: 22px;
    overflow: hidden;
    background: var(--card-white);
    box-shadow: 0 10px 28px rgba(0,0,0,0.35);
  }
  .card--front { top: 50px; }
  .card--back { top: 462px; }

  /* Front */
  .brand-mark {
    position: absolute;
    left: 48px;
    top: 160px;
    display: flex;
    align-items: center;
    gap: 12px;
    font-family: var(--display-font);
    font-size: 26px;
    color: var(--green);
  }
  .brand-mark__dot {
    width: 22px; height: 22px; border-radius: 50%;
    background: var(--green);
  }
  .pitch {
    position: absolute;
    right: 36px;
    top: 118px;
    text-align: right;
    font-size: 17px;
    line-height: 1.45;
  }
  .pitch__headline {
    display: inline-block;
    border: 2px solid var(--ink);
    border-radius: 16px;
    padding: 2px 14px;
    font-size: 17px;
    margin-bottom: 4px;
  }
  .accent { color: var(--green); }
  .accent-strong { color: var(--green); font-family: var(--display-font); font-size: 15px; }
  .benefits { list-style: none; margin-bottom: 4px; }
  .benefits li::after {
    content: "";
    display: inline-block;
    width: 7px; height: 7px; border-radius: 50%;
    background: var(--green);
    margin-left: 10px;
    vertical-align: middle;
  }
  .benefits li { padding-right: 0; }
  .pitch__close { padding-right: 17px; }

  /* Back */
  .back-panel { position: absolute; inset: 0; }
  .holder {
    position: absolute;
    left: 0;
    top: 44px;
    padding-left: 46px;
  }
  .holder::before {
    content: "";
    position: absolute;
    left: 0; top: 8px;
    width: 34px; height: 38px;
    background: var(--card-black);
  }
  .holder__name {
    font-family: var(--display-font);
    font-size: 22px;
    color: var(--green);
    letter-spacing: 0.5px;
  }
  .holder__role {
    font-family: var(--display-font);
    font-size: 11px;
    color: var(--ink);
    letter-spacing: 0.5px;
  }
  .back-brand {
    position: absolute;
    right: 40px;
    top: 60px;
    text-align: right;
  }
  .back-brand__name {
    display: flex;
    align-items: center;
    justify-content: flex-end;
    gap: 10px;
    font-family: var(--display-font);
    font-size: 30px;
    color: #ffffff;
  }
  .back-brand__dot {
    width: 20px; height: 20px; border-radius: 50%;
    background: var(--green);
  }
  .back-brand__tagline {
    font-size: 10px;
    color: var(--muted);
    margin-top: 4px;
  }
  .contact {
    position: absolute;
    right: 40px;
    top: 160px;
    list-style: none;
    text-align: right;
    color: #ffffff;
    font-size: 18px;
    line-height: 1.5;
  }
  .contact li { display: flex; align-items: center; justify-content: flex-end; gap: 12px; }
  .contact svg { width: 14px; height: 14px; flex: none; }
  .offer {
    position: absolute;
    right: 40px;
    top: 300px;
    font-size: 19px;
    color: var(--green);
  }
  .offer__label { font-family: var(--display-font); font-size: 16px; }
  .offer__free { font-family: var(--display-font); font-size: 16px; color: #ffffff; }
  .offer__num { color: #ffffff; font-size: 22px; }
</style>
</head>
<body>

  <section class="card card--front" aria-label="Card front">
    <div class="brand-mark">
      <span class="brand-mark__dot"></span>
      <span>Clearpath Coaching</span>
    </div>
    <div class="pitch">
      <p class="pitch__headline"><span class="accent">STRUGGLING</span> WITH YOUR <span class="accent-strong">FINANCES?</span></p>
      <ul class="benefits">
        <li>Learn to become debt free</li>
        <li>Discover the power of cash</li>
        <li>Control your money instead of it controlling you</li>
      </ul>
      <p class="pitch__close">Let us help you achieve a new level of financial <span class="accent-strong">FREEDOM!</span></p>
    </div>
  </section>

  <section class="card card--back" aria-label="Card back">
    <svg class="back-panel" width="680" height="388" viewBox="0 0 680 388">
      <path d="M340 0 Q255 200 310 388 L680 388 L680 0 Z" fill="var(--card-black)"/>
    </svg>

    <div class="holder">
      <p class="holder__name">DANIEL R. HAYES</p>
      <p class="holder__role">PERSONAL FINANCIAL COACH</p>
    </div>

    <div class="back-brand">
      <p class="back-brand__name"><span class="back-brand__dot"></span>Clearpath Coaching</p>
      <p class="back-brand__tagline">Achieve a new level of personal freedom</p>
    </div>

    <ul class="contact">
      <li>(555) 014-2287
        <svg viewBox="0 0 14 14"><rect x="3.5" y="1" width="7" height="12" rx="1.5" fill="none" stroke="var(--green)" stroke-width="1.4"/></svg>
      </li>
      <li>daniel@clearpathcoaching.com
        <svg viewBox="0 0 14 14"><rect x="1" y="3" width="12" height="8" fill="none" stroke="var(--green)" stroke-width="1.4"/><path d="M1 3 L7 8 L13 3" fill="none" stroke="var(--green)" stroke-width="1.4"/></svg>
      </li>
      <li><span>www.<span class="accent">clearpathcoaching.com</span></span>
        <svg viewBox="0 0 14 14"><circle cx="7" cy="7" r="6" fill="var(--green)"/><path d="M1 7 H13 M7 1 V13" stroke="var(--card-black)" stroke-width="1"/></svg>
      </li>
    </ul>

    <p class="offer"><span class="offer__label">SPECIAL OFFER!</span> <span class="offer__free">FREE</span> <span class="offer__num">30</span> minute consultation</p>
  </section>

</body>
</html>
```